Business Card: RW Office Partners - Your organised problem solver

Business Name: RW Office Partners
Website: www.rwofficepartners.com.au
Email: marisol@rwofficepartners.com.au
Mobile: 61 482 907 236
Facebook: @rwofficepartners
Instrgram: @rwofficepartners

Brading Colours:
HEX
#986474
#ddccd3
#7a8498
#c9d8e4
#000000
#ffffff

Tag Line: Your organised problem solver

Link to DRAFT website:
https://deskhelpcollective.wixsite.com/rw-office-partners

About Page from the website:
My name is Marisol Wrenfield, and I would love to assist you to become more productive in your day to day and achieve your business and personal goals.
My mission is to give you time, time to work on the important tasks of your business or to be able to spend more time with your family. I will take on the tasks you don’t have time for, don’t know well or simply don’t like to do.
I have an extensive background in Administration, Tender Coordination, Document Control, WHS and Quality Management working primarily in the Construction, Mining and Corporate World.
I am passionate about being organised, having order and making things in your life (and mine) easier! I love to watch something unfold and grow into something amazing! I am known for being the go-to problem solver, the organiser of all things, producing high standards of work even under pressure. I’m also a confident communicator, and I understand that you’re busy running your business.

Target Market(s)

Small to Medium Business who require assistance in their business by a virtual assistant.

Industry/Entity Type

Virtual Assistant

Contact Information for Business Card

Mobile: 61 482 907 236

Font styles to use
Sans Serif

Colors
ffffff

Requirements
Must have
• Branding Colours as outlined.
Contact Details as outlined.
Logo as provided.
Proper contact details - mobile, facebook, instragm, website.
Simple, Elegant, very clean looking.
Should not have
• Note cute with pictures.
Not too girly as still want to market to construction companies.

```html
<!DOCTYPE html>
<html lang="en">
<head>
<meta charset="utf-8">
<title>RW Office Partners – Business Card</title>
<link rel="stylesheet" href="https://fonts.googleapis.com/css2?family=Roboto:wght@400;500&display=swap">
<style>
  :root {
    --mauve: #986474;
    --mauve-soft: #ddccd3;
    --slate: #7a8498;
    --slate-soft: #c9d8e4;
    --ink: #333438;
    --paper: #ffffff;
    --backdrop: #e9e9eb;
  }
  * { margin: 0; padding: 0; box-sizing: border-box; }
  html, body { width: 1200px; height: 1200px; overflow: hidden; }
  body {
    background: var(--backdrop);
    font-family: "Roboto", Arial, sans-serif;
    color: var(--ink);
    position: relative;
  }
  .card {
    position: absolute;
    width: 712px;
    height: 417px;
    background: var(--paper);
    border-radius: 22px;
    overflow: hidden;
    box-shadow: 0 2px 6px rgba(0,0,0,0.08);
  }
  .card--front { left: 238px; top: 120px; }
  .card--back  { left: 230px; top: 645px; }

  .wordmark {
    position: absolute;
    font-weight: 500;
    color: var(--mauve);
    white-space: nowrap;
    letter-spacing: 0.5px;
  }
  .card--front .wordmark {
    left: 0; right: 0; top: 152px;
    text-align: center;
    font-size: 54px;
  }
  .card--back .wordmark {
    left: 40px; top: 62px;
    font-size: 46px;
  }

  .social-row {
    position: absolute;
    left: 0; right: 0; top: 350px;
    display: flex;
    justify-content: center;
    gap: 18px;
    font-size: 18px;
  }
  .social { display: flex; align-items: center; gap: 10px; }
  .social-mark {
    width: 15px; height: 15px;
    border-radius: 3px;
    background: var(--mauve);
    display: inline-block;
  }

  .front-bands { position: absolute; left: 0; bottom: 0; width: 100%; height: 15px; display: flex; }
  .front-bands .band--mauve { width: 357px; background: var(--mauve); }
  .front-bands .band--slate { flex: 1; background: var(--slate); }

  .person { position: absolute; left: 39px; top: 234px; }
  .person-name { font-size: 28px; font-weight: 500; color: var(--mauve); line-height: 1.1; }
  .person-role { font-size: 19px; margin-top: 6px; }

  .back-social { position: absolute; left: 40px; top: 340px; font-size: 17px; }
  .back-social .social { margin-bottom: 5px; gap: 12px; }

  .contact-list { position: absolute; left: 337px; top: 236px; list-style: none; font-size: 19px; }
  .contact-list li { display: flex; align-items: center; gap: 14px; height: 26px; }
  .contact-list svg { width: 17px; height: 17px; fill: var(--mauve); }

  .back-bands { position: absolute; left: 0; top: 0; width: 712px; height: 417px; }
  .tagline {
    position: absolute;
    left: 338px; top: 378px;
    font-size: 18px;
    color: var(--paper);
  }
</style>
</head>
<body>

<section class="card card--front" aria-label="Card front">
  <div class="wordmark">RW Office Partners</div>
  <div class="social-row">
    <span class="social"><span class="social-mark"></span>@rwofficepartners</span>
    <span class="social"><span class="social-mark"></span>@rwofficepartners</span>
  </div>
  <div class="front-bands"><div class="band--mauve"></div><div class="band--slate"></div></div>
</section>

<section class="card card--back" aria-label="Card back">
  <svg class="back-bands" viewBox="0 0 712 417" aria-hidden="true">
    <rect x="0" y="399" width="712" height="18" fill="var(--slate)"/>
    <path d="M275 417 L295 365 L712 365 L712 417 Z" fill="var(--mauve)"/>
  </svg>
  <div class="wordmark">RW Office Partners</div>

  <div class="person">
    <div class="person-name">Marisol Wrenfield</div>
    <div class="person-role">Virtual Assistant</div>
  </div>

  <ul class="contact-list">
    <li>
      <svg viewBox="0 0 20 20"><path d="M3 7c0-2 3-3 7-3s7 1 7 3v1.5h-3.5V7h-7v1.5H3z M5 10h10l1.5 6h-13z"/></svg>
      61 482 907 236
    </li>
    <li>
      <svg viewBox="0 0 20 20"><path d="M2 5h16v10H2z" fill="var(--mauve)"/><path d="M2.5 5.5 10 11l7.5-5.5" stroke="#fff" stroke-width="1.4" fill="none"/></svg>
      marisol@rwofficepartners.com.au
    </li>
    <li>
      <svg viewBox="0 0 20 20"><circle cx="10" cy="10" r="7.5" fill="none" stroke="var(--mauve)" stroke-width="1.6"/><path d="M2.5 10h15M10 2.5c-3 3.5-3 11.5 0 15M10 2.5c3 3.5 3 11.5 0 15" fill="none" stroke="var(--mauve)" stroke-width="1.4"/></svg>
      www.rwofficepartners.com.au
    </li>
  </ul>

  <div class="back-social">
    <div class="social"><span class="social-mark"></span>@rwofficepartners</div>
    <div class="social"><span class="social-mark"></span>@rwofficepartners</div>
  </div>

  <div class="tagline">Your organised problem solver</div>
</section>

</body>
</html>
```